Business card design Needed for new logo / Construction business, home extensions and new builds

We need a business card design using our new logo files which i will attach to this project :)

We are a small construction business specialising in home extensions, new builds and property development. We are very ambitious and would appreciate professional and elegant designs for our new business card.

Very serious about using the services on MakerQuarry and recently acquired our new logo from here :)

Please get involved, i will feedback when i can as i am very busy but can respond daily, thanks

Target Market(s)

People that want to build onto their houses, new building developments or adding too their existing property

Industry/Entity Type

Construction

Contact Information for Business Card

Renwick Tolliver Construction, Lionel Ashby (Managing Director), Tel 07822254961, email - info@renwick-tolliver, www.renwick-tolliver.co.uk

Colors

Designer to choose colors to be used in the design.

Requirements
Must have
• I like a deep grey on the back please. A lot of you have provided black from and back, try mixing things up a little. The black looks cool 😎 Thanks

```html
<!DOCTYPE html>
<html lang="en">
<head>
<meta charset="utf-8">
<title>Renwick Tolliver Construction – Business Card</title>
<link href="https://fonts.googleapis.com/css2?family=Montserrat:wght@300;400;600;700&display=swap" rel="stylesheet">
<style>
  :root {
    --backdrop: #e4e4e2;
    --card-white: #ffffff;
    --ink: #1c1c1c;
    --ink-soft: #333333;
    --deep-grey: #1e1e1e;
    --deep-grey-edge: #0e0e0e;
    --gold: #d9a520;
    --sketch-light: #f2f2f2;
    --sketch-mid: #d2d2d2;
    --sketch-dark: #a8a8a8;
  }
  * { box-sizing: border-box; margin: 0; padding: 0; }
  html, body {
    width: 1200px; height: 846px; overflow: hidden;
    background: var(--backdrop);
    font-family: "Montserrat", Arial, sans-serif;
  }
  .canvas { position: relative; width: 1200px; height: 846px; }
  .card {
    position: absolute; left: 347px; width: 509px; height: 291px;
    box-shadow: 8px 10px 14px rgba(0,0,0,0.14);
    overflow: hidden;
  }
  .card--front { top: 99px; background: var(--card-white); }
  .card--back { top: 457px; }

  /* front */
  .front__artwork {
    position: absolute; right: 0; top: 0; width: 286px; height: 100%;
    background:
      linear-gradient(180deg, var(--sketch-light) 0%, var(--sketch-mid) 45%, var(--sketch-dark) 72%, var(--sketch-mid) 100%);
    -webkit-mask-image: linear-gradient(90deg, transparent 0%, rgba(0,0,0,0.6) 22%, #000 45%);
            mask-image: linear-gradient(90deg, transparent 0%, rgba(0,0,0,0.6) 22%, #000 45%);
  }
  .brand {
    position: absolute; left: 23px; top: 46px; width: 170px;
    text-align: center; color: var(--ink); font-weight: 600;
  }
  .brand__mark { width: 40px; height: 40px; margin: 0 auto 20px; background: var(--ink); }
  .brand__name { display: block; font-size: 11px; letter-spacing: 0.6px; line-height: 1.2; white-space: nowrap; }
  .brand__sub {
    display: flex; align-items: center; justify-content: center; gap: 6px;
    font-size: 9.5px; letter-spacing: 1.2px; line-height: 1.3;
  }
  .brand__sub::before, .brand__sub::after {
    content: ""; width: 14px; height: 1px; background: currentColor;
  }

  .person { position: absolute; left: 41px; top: 156px; color: var(--ink); }
  .person__name { font-size: 16px; font-weight: 700; letter-spacing: 0.2px; }
  .person__role { font-size: 11.5px; font-weight: 400; color: var(--ink-soft); letter-spacing: 0.3px; margin-top: 1px; }

  .contact { position: absolute; left: 40px; top: 199px; list-style: none; }
  .contact__item {
    display: flex; align-items: center; height: 20.5px;
    font-size: 15.5px; font-weight: 300; color: var(--ink);
  }
  .contact__icon {
    width: 17px; height: 17px; margin-right: 5px; flex: none;
    background: var(--ink); display: flex; align-items: center; justify-content: center;
  }
  .contact__icon svg { width: 11px; height: 11px; }

  /* back */
  .back__texture {
    position: absolute; inset: 0;
    background:
      radial-gradient(ellipse at 30% 30%, #2a2a2a 0%, transparent 60%),
      linear-gradient(135deg, var(--deep-grey) 0%, #181818 60%, var(--deep-grey-edge) 100%);
  }
  .back__brand {
    position: absolute; left: 0; right: 0; top: 79px;
    text-align: center; color: var(--gold); font-weight: 600;
  }
  .back__mark { width: 64px; height: 64px; margin: 0 auto 51px; background: var(--gold); }
  .back__name { display: block; font-size: 26px; letter-spacing: 0.8px; line-height: 1.1; white-space: nowrap; }
  .back__sub {
    display: flex; align-items: center; justify-content: center; gap: 14px;
    font-size: 19px; letter-spacing: 2.5px; line-height: 1.4;
  }
  .back__sub::before, .back__sub::after {
    content: ""; width: 30px; height: 2px; background: currentColor;
  }
</style>
</head>
<body>
<main class="canvas">
  <section class="card card--front">
    <div class="front__artwork" role="img" aria-label="Pencil sketch of a detached two-storey house over architectural floor plans"></div>

    <div class="brand">
      <div class="brand__mark"></div>
      <span class="brand__name">RENWICK TOLLIVER</span>
      <span class="brand__sub">CONSTRUCTION</span>
    </div>

    <div class="person">
      <p class="person__name">Lionel Ashby</p>
      <p class="person__role">Managing Director</p>
    </div>

    <ul class="contact">
      <li class="contact__item">
        <span class="contact__icon"><svg viewBox="0 0 24 24"><path fill="#fff" d="M6.6 10.8a15 15 0 0 0 6.6 6.6l2.2-2.2a1 1 0 0 1 1-.25 11.4 11.4 0 0 0 3.6.57 1 1 0 0 1 1 1V20a1 1 0 0 1-1 1A17 17 0 0 1 3 4a1 1 0 0 1 1-1h3.5a1 1 0 0 1 1 1c0 1.25.2 2.45.57 3.6a1 1 0 0 1-.25 1z"/></svg></span>
        07822 254 961
      </li>
      <li class="contact__item">
        <span class="contact__icon"><svg viewBox="0 0 24 24"><rect x="2" y="5" width="20" height="14" fill="none" stroke="#fff" stroke-width="2"/><path d="M2 5l10 8 10-8M2 19l7-7M22 19l-7-7" fill="none" stroke="#fff" stroke-width="1.6"/></svg></span>
        info@renwick-tolliver.co.uk
      </li>
      <li class="contact__item">
        <span class="contact__icon"><svg viewBox="0 0 24 24"><g fill="none" stroke="#fff" stroke-width="1.6"><circle cx="12" cy="12" r="10"/><ellipse cx="12" cy="12" rx="4.5" ry="10"/><path d="M2 12h20M4 7h16M4 17h16"/></g></svg></span>
        www.renwick-tolliver.co.uk
      </li>
    </ul>
  </section>

  <section class="card card--back">
    <div class="back__texture" role="img" aria-label="Deep grey embossed abstract pattern of overlapping angular strokes"></div>
    <div class="back__brand">
      <div class="back__mark"></div>
      <span class="back__name">RENWICK TOLLIVER</span>
      <span class="back__sub">CONSTRUCTION</span>
    </div>
  </section>
</main>
</body>
</html>
```